MRT Property - Business Cards

Looking for a business card & general letterhead, signage etc design for our new logo.

Colours:
000a20
0056a2
00b5ef
0088ce
68cef2

Fonts:
Poppins
Karla

Please keep look and feel of new brand - example in the zip package I sent.

```html
<!DOCTYPE html>
<html lang="en">
<head>
<meta charset="utf-8">
<title>MRT Property – Business Cards</title>
<link rel="stylesheet" href="https://fonts.googleapis.com/css2?family=Poppins:wght@400;500;700&family=Karla:wght@400;500&display=swap">
<style>
  :root {
    --navy: #0b1120;
    --deep-blue: #0056a2;
    --cyan: #00b5ef;
    --mid-blue: #0088ce;
    --sky: #68cef2;
    --white: #ffffff;
    --stage: #2b2c2e;
  }
  * { box-sizing: border-box; margin: 0; padding: 0; }
  html, body { width: 1200px; height: 880px; overflow: hidden; }
  body {
    background: var(--stage);
    display: flex;
    align-items: center;
    justify-content: center;
    gap: 40px;
    font-family: "Poppins", sans-serif;
  }
  .card {
    position: relative;
    width: 540px;
    height: 310px;
    border-radius: 20px;
    overflow: hidden;
  }
  .card-front {
    background: var(--sky);
    display: flex;
    align-items: center;
    justify-content: center;
  }
  .brand {
    display: flex;
    align-items: center;
    gap: 16px;
    font-family: "Poppins", sans-serif;
    font-weight: 700;
    white-space: nowrap;
  }
  .brand-mark { border-radius: 50%; flex: none; }
  .card-front .brand { font-size: 50px; color: var(--white); }
  .card-front .brand-mark { width: 44px; height: 44px; background: var(--white); }

  .card-back { background: var(--navy); color: var(--white); }
  .card-back .brand {
    position: absolute; left: 34px; top: 42px;
    font-size: 30px; color: var(--deep-blue); gap: 10px;
  }
  .card-back .brand-mark { width: 28px; height: 28px; background: var(--cyan); }

  .holder {
    position: absolute; right: 0; top: 44px;
    display: flex; align-items: stretch; gap: 10px;
    text-align: right;
  }
  .holder-name {
    font-weight: 500; font-size: 19px; letter-spacing: 1px;
    color: var(--deep-blue); text-transform: uppercase; line-height: 1.2;
  }
  .holder-role { font-family: "Karla", sans-serif; font-size: 14px; line-height: 1.3; }
  .holder-bar { width: 12px; background: var(--deep-blue); }

  .contact {
    position: absolute; left: 70px; bottom: 34px;
    font-family: "Karla", sans-serif; font-size: 15px; line-height: 1.35;
  }
  .address { margin-bottom: 18px; }
  .contact-list { list-style: none; }
  .contact-list li { display: flex; align-items: center; gap: 8px; }
  .contact-list svg { width: 13px; height: 13px; fill: var(--cyan); flex: none; }
</style>
</head>
<body>
  <section class="card card-front">
    <div class="brand"><span class="brand-mark"></span>MRT Property</div>
  </section>

  <section class="card card-back">
    <div class="brand"><span class="brand-mark"></span>MRT Property</div>

    <div class="holder">
      <div>
        <p class="holder-name">Daniel Reyes</p>
        <p class="holder-role">Managing Director</p>
      </div>
      <span class="holder-bar"></span>
    </div>

    <div class="contact">
      <p class="address">Your address, City<br>State, Zip 1234</p>
      <ul class="contact-list">
        <li>
          <svg viewBox="0 0 24 24" aria-hidden="true"><path d="M6.6 10.8a15.1 15.1 0 0 0 6.6 6.6l2.2-2.2a1 1 0 0 1 1-.25 11.4 11.4 0 0 0 3.6.57 1 1 0 0 1 1 1V20a1 1 0 0 1-1 1A17 17 0 0 1 3 4a1 1 0 0 1 1-1h3.5a1 1 0 0 1 1 1c0 1.25.2 2.45.57 3.57a1 1 0 0 1-.25 1z"/></svg>
          123 456 789
        </li>
        <li>
          <svg viewBox="0 0 24 24" aria-hidden="true"><path d="M2 5h20v14H2zm2 2v.5l8 5 8-5V7l-8 5z"/></svg>
          info@yourmail.com
        </li>
        <li>
          <svg viewBox="0 0 24 24" aria-hidden="true"><circle cx="12" cy="12" r="10"/></svg>
          www.yourwebsite.com
        </li>
      </ul>
    </div>
  </section>
</body>
</html>
```